Business card por a urban DJ, up scale audience target

Need a sober design, modern, conservative colors but i can consider some options, y play rnb, hip hop, EDM and top40.

Business card for contact and personal info, double sided, use logo attrached please; im 42 so i need a card acording to my age an target audience.

Target Market(s)

Adult people, up scale audience

Industry/Entity Type

Music Download

Contact Information for Business Card

Cel (318) 4207265518 www.lumadrift.com

Requirements
Must have
• open mind
Nice to have
• open mind
Should not have
• DJ

```html
<!DOCTYPE html>
<html lang="en">
<head>
<meta charset="utf-8">
<title>Lumadrift – Business Card</title>
<link href="https://fonts.googleapis.com/css2?family=Open+Sans:wght@400;700;800&display=swap" rel="stylesheet">
<style>
  :root{
    --page:#e9e7e3;
    --card-white:#f7f7f7;
    --ink:#3a3a3a;
    --ink-soft:#555;
    --faint:#dcdcdc;
    --teal:#0f7aa6;
    --teal-dark:#0a5f84;
    --charcoal:#2b2b2b;
    --charcoal-deep:#1c1c1c;
    --paper:#ffffff;
  }
  *{margin:0;padding:0;box-sizing:border-box}
  html,body{width:1200px;height:892px;overflow:hidden}
  body{background:var(--page);font-family:"Open Sans",Arial,sans-serif;position:relative}
  .card{position:absolute;top:291px;width:540px;height:310px;border-radius:4px;overflow:hidden;box-shadow:0 6px 18px rgba(0,0,0,.18)}
  .card--front{left:40px;background:var(--card-white)}
  .card--back{left:620px;background:linear-gradient(135deg,var(--charcoal) 0%,var(--charcoal-deep) 100%)}

  .front-watermark{position:absolute;left:190px;top:26px;font-weight:800;font-size:92px;color:var(--faint);letter-spacing:2px;line-height:1}
  .front-curve{position:absolute;inset:0}
  .front-brand{position:absolute;left:34px;top:112px;display:flex;align-items:center;gap:10px}
  .front-brand__mark{width:18px;height:18px;background:var(--ink)}
  .front-brand__name{font-weight:800;font-size:44px;color:var(--ink);line-height:1;letter-spacing:1px}
  .holder{position:absolute;left:34px;top:172px}
  .holder__name{font-weight:700;font-size:19px;color:var(--ink);line-height:1.15}
  .holder__role{font-size:12px;color:var(--ink-soft);line-height:1.3}
  .contacts{position:absolute;left:34px;top:220px;list-style:none}
  .contacts li{display:flex;align-items:center;gap:8px;font-size:11.5px;color:var(--ink);line-height:1;margin-bottom:6px}
  .contacts li:last-child{margin-bottom:0}
  .contacts svg{width:11px;height:11px;flex:none}

  .back-brand{position:absolute;left:150px;top:104px;display:flex;align-items:center;gap:16px}
  .back-brand__mark{width:28px;height:28px;background:var(--paper)}
  .back-brand__name{font-weight:800;font-size:90px;color:var(--paper);line-height:1;letter-spacing:2px}
  .back-url{position:absolute;left:40px;bottom:34px;display:flex;align-items:center;gap:10px;font-size:12px;color:#cfcfcf}
  .back-url__rule{width:70px;height:1px;background:#9a9a9a}
</style>
</head>
<body>

<section class="card card--front" aria-label="Card front">
  <div class="front-watermark" aria-hidden="true">LUMA</div>
  <svg class="front-curve" viewBox="0 0 540 310" preserveAspectRatio="none" aria-hidden="true">
    <defs>
      <linearGradient id="tealFade" x1="0" y1="0" x2="1" y2="1">
        <stop offset="0" stop-color="#1690c2"/>
        <stop offset="1" stop-color="#0a5f84"/>
      </linearGradient>
    </defs>
    <path d="M300 0 C 400 60 430 190 410 310 L540 310 L540 0 Z" fill="#2b2b2b"/>
    <path d="M318 0 C 430 50 470 170 470 310 L540 310 L540 0 Z" fill="url(#tealFade)"/>
  </svg>
  <div class="front-brand">
    <span class="front-brand__mark"></span>
    <span class="front-brand__name">LUMA</span>
  </div>
  <div class="holder">
    <p class="holder__name">Marcus Hale</p>
    <p class="holder__role">Director</p>
  </div>
  <ul class="contacts">
    <li><svg viewBox="0 0 12 12"><rect width="12" height="12" rx="2" fill="#3a3a3a"/><path d="M3.5 3h1.5l.7 1.6-.9.6a4 4 0 0 0 2 2l.6-.9 1.6.7V8.5c0 .4-.4.6-.8.6A5.6 5.6 0 0 1 3 3.8c0-.4.2-.8.5-.8z" fill="#fff"/></svg>(318) 4207265518</li>
    <li><svg viewBox="0 0 12 12"><rect width="12" height="12" rx="2" fill="#3a3a3a"/><rect x="2.5" y="3.5" width="7" height="5" fill="none" stroke="#fff" stroke-width=".9"/><path d="M2.5 3.5 6 6.3 9.5 3.5" fill="none" stroke="#fff" stroke-width=".9"/></svg>info@lumadrift.com</li>
    <li><svg viewBox="0 0 12 12"><rect width="12" height="12" rx="2" fill="#3a3a3a"/><circle cx="6" cy="6" r="3.4" fill="none" stroke="#fff" stroke-width=".9"/><path d="M2.6 6h6.8M6 2.6c-1.6 2-1.6 4.8 0 6.8M6 2.6c1.6 2 1.6 4.8 0 6.8" fill="none" stroke="#fff" stroke-width=".7"/></svg>www.lumadrift.com</li>
    <li><svg viewBox="0 0 12 12"><rect width="12" height="12" rx="2" fill="#3a3a3a"/><path d="M6 2.3a2.6 2.6 0 0 0-2.6 2.6C3.4 7 6 9.7 6 9.7S8.6 7 8.6 4.9A2.6 2.6 0 0 0 6 2.3z" fill="#fff"/><circle cx="6" cy="4.9" r=".9" fill="#3a3a3a"/></svg>PO Box 4810 Ashford Vale SA 5072</li>
  </ul>
</section>

<section class="card card--back" aria-label="Card back">
  <div class="back-brand">
    <span class="back-brand__mark"></span>
    <span class="back-brand__name">LUMA</span>
  </div>
  <div class="back-url">
    <span>www.lumadrift.com</span>
    <span class="back-url__rule"></span>
  </div>
</section>

</body>
</html>
```